Dashboard Elements

Hello – looking for someone to create dashboard elements.
I’ve already basically designed all these elements – but I need someone to take what I’ve designed and make it look like an actual dashboard UI, like an app - assuming using some kind of dashboard UI kit (but however you would like to get it done is fine). It can look just like mine or try something different, as long as it matches the color scheme webpage that I’m going to out it on – see the page here. I’m ok with making it dark, maybe that would look better – again as long as it matches the webpage (https://www.plandeck.io/file/7QxKtr2BwLpZnVe4Hs8Mc1/Webpage-with-placeholders?node-id=0%3A1). Please note, you do not need to put anything on the webpage or do anything with this Figma file, this is just a reference so you can color/stylize it accordingly.

The attached Powerpoint file has everything you need - make sure to zoom all the way out to see everything on the slides.

Here are the Dashboard elements needed (this will all make sense when you look at the PPT):
Dashboard 1
Dashboard 1 – expanded view A
Dashboard 1 – expanded view B
View Source button by itself
Source Document Viewer 1 and 2 (these are exactly the same just with a different image inside)*
Dashboard 2 (only slightly different than Dashboard 1, just extended with extra headings
Table of Contents
Searchbar and Source Doc by itself
*the documents in the source document viewers should still look like documents - they don’t need to look like part of the UI, because this is a document viewer – you can restyle/recolor if necessary or just leave these as is.
- Colors must match color scheme of webpage, attached and on Figma link (images there currently are only placeholders) – ok to go dark as long as it matches
- Must look sleek, clean, realistic
- Don’t add any pictures of people or change the text.
- In case it’s not clear, this is what I mean by the concept of Dashboard UI - https://www.notavia.net/shard/s7/sh/8fad21bc-14e9-4a7c-b2d0-5c3e9f71a604/92c4e1b7a05d3f68e1c2b947d0a3f815
- Must be sent in an editable file, I may need to be edit text and other elements
- If you are going to send a sample, please make sure it’s part of the dashboard itself, not just the table of contents etc

Ideally hoping to find someone I can continue working with as I'll have a lot more graphic design work needed coming up.

Thank you!

```html
<!DOCTYPE html>
<html lang="en">
<head>
<meta charset="utf-8">
<title>Compendium C-CDA – Summarized and Linked to Key Insights</title>
<link rel="stylesheet" href="https://fonts.googleapis.com/css2?family=Roboto:ital,wght@0,300;0,400;0,500;0,700;1,400&family=Saira:ital,wght@0,300;0,400;0,500;1,300;1,400&display=swap">
<style>
  :root {
    --bg: #0c0b19;
    --bg-card: #17162c;
    --line: #3a3762;
    --teal: #2fd3c2;
    --teal-deep: #1795a8;
    --blue: #1f8fd6;
    --purple: #6a4fe0;
    --purple-deep: #3a2a9a;
    --panel: #2b333f;
    --panel-head: #3b4556;
    --ink: #ffffff;
    --ink-soft: #c9c9d9;
    --ink-dim: #8d93a6;
  }
  * { box-sizing: border-box; margin: 0; padding: 0; }
  html, body { width: 768px; height: 1200px; overflow: hidden; }
  body {
    position: relative;
    background:
      radial-gradient(ellipse 220px 260px at -40px 300px, rgba(30,140,150,.45), transparent 70%),
      radial-gradient(ellipse 200px 220px at -20px 830px, rgba(40,150,150,.55), transparent 70%),
      radial-gradient(ellipse 200px 200px at 800px -20px, rgba(110,80,190,.55), transparent 70%),
      radial-gradient(ellipse 160px 260px at 800px 560px, rgba(40,130,140,.35), transparent 70%),
      radial-gradient(ellipse 200px 200px at 800px 1220px, rgba(110,80,190,.5), transparent 70%),
      var(--bg);
    font-family: "Roboto", sans-serif;
    color: var(--ink);
  }
  .abs { position: absolute; }
  .decor { position: absolute; left: 0; top: 0; }

  /* Intro */
  .intro-title { left: 56px; top: 140px; font-family: "Saira", sans-serif; font-size: 11.5px; letter-spacing: 1px; font-weight: 400; }
  .intro-text { left: 56px; top: 166px; width: 260px; font-size: 11px; line-height: 17px; font-weight: 300; color: var(--ink-soft); }
  .ccda-tag {
    left: 451px; top: 145px; width: 59px; height: 26px; border-radius: 4px;
    background: linear-gradient(180deg, #2bb4c7, #1b7fa6);
    font-family: "Saira", sans-serif; font-size: 12px; letter-spacing: 1px;
    display: flex; align-items: center; justify-content: center;
  }

  /* Table of contents panel */
  .toc-shadow, .toc {
    left: 520px; top: 54px; width: 132px; height: 242px; transform: skewX(-15deg); border-radius: 4px;
  }
  .toc-shadow { background: var(--purple-deep); left: 528px; top: 60px; }
  .toc { background: linear-gradient(180deg, #24303a, #1b2229); padding: 8px 8px; }
  .toc-head, .toc-item {
    display: flex; align-items: center; gap: 7px; font-family: "Saira", sans-serif; font-style: italic;
    font-size: 8px; height: 17.6px;
  }
  .toc-head { border: 1px solid var(--teal); border-radius: 2px; padding: 0 5px; font-size: 6px; height: 16px; margin-bottom: 6px; }
  .toc-head .caret { margin-left: auto; width: 0; height: 0; border: 3px solid transparent; border-bottom-color: var(--teal); border-top: 0; }
  .toc-item.active { border: 1px solid var(--teal); border-radius: 2px; padding: 0 5px; color: var(--teal); font-weight: 500; margin-bottom: 3px; font-size: 7px; }
  .toc-icon { width: 11px; height: 11px; border-radius: 2px; background: linear-gradient(135deg, #3fd8e6, #1a78b2); flex: none; }

  /* Insights card */
  .insights { left: 53px; top: 388px; width: 664px; height: 375px; border-radius: 8px;
    background: linear-gradient(160deg, rgba(40,38,70,.55), rgba(24,26,44,.4)); border: 1px solid rgba(255,255,255,.07); }
  .insights-title { left: 0; width: 768px; top: 428px; text-align: center; font-family: "Saira", sans-serif; font-weight: 300; font-size: 27px; line-height: 33px; letter-spacing: 3px; }
  .insights-text { left: 164px; width: 440px; top: 508px; text-align: center; font-size: 11px; line-height: 17px; font-weight: 300; color: var(--ink-soft); }

  /* Dashboard summary */
  .dash-shadow, .dash { left: 222px; top: 600px; width: 330px; height: 230px; border-radius: 22px; transform: skewX(-7deg); }
  .dash-shadow { background: var(--purple-deep); left: 228px; top: 606px; }
  .dash { background: var(--panel); overflow: hidden; }
  .dash-inner { transform: skewX(7deg); position: relative; height: 100%; }
  .brand { left: 20px; top: 17px; display: flex; align-items: center; gap: 4px; font-size: 7px; letter-spacing: .5px; }
  .brand-mark { width: 7px; height: 7px; background: var(--teal); }
  .patient { right: 20px; top: 14px; font-size: 4.5px; line-height: 7px; color: var(--ink-soft); font-style: italic; }
  .dash-title { left: 0; width: 100%; top: 33px; text-align: center; color: var(--teal); font-family: "Saira", sans-serif; font-style: italic; font-size: 10px; }
  .hcc { left: 20px; top: 52px; color: var(--teal); font-family: "Saira", sans-serif; font-style: italic; font-size: 9px; display: flex; align-items: center; gap: 5px; }
  .hcc::before { content: ""; border: 2.5px solid transparent; border-top: 3px solid var(--teal); margin-top: 3px; }
  .raf-line { right: 20px; top: 55px; font-size: 5.5px; font-style: italic; }
  .raf-line .teal { color: var(--teal); }
  table.hcc-table { position: absolute; left: 0; top: 72px; width: 100%; border-collapse: collapse; font-size: 6.2px; font-style: italic; }
  .hcc-table th { background: var(--panel-head); height: 18px; font-weight: 700; text-align: left; font-size: 5.5px; }
  .hcc-table td { height: 24px; border-bottom: 1px solid #232a35; }
  .hcc-table .code { color: var(--teal); padding-left: 26px; width: 64px; font-weight: 500; }
  .hcc-table .cond { width: 150px; text-align: center; }
  .hcc-table .cat { width: 46px; text-align: center; }
  .hcc-table .raf { color: var(--teal); font-weight: 500; text-align: center; width: 36px; }
  .hcc-table .arrow { color: var(--teal); font-size: 5px; padding-left: 6px; }
  .hover-ring { left: 485px; top: 761px; width: 24px; height: 24px; border-radius: 50%; border: 1.5px solid var(--teal); box-shadow: 0 0 0 3px rgba(47,211,194,.18); }
  .hover-badge { left: 464px; top: 797px; width: 77px; height: 15px; border-radius: 2px; background: var(--purple); font-size: 7.5px; font-weight: 500; letter-spacing: .4px; display: flex; align-items: center; justify-content: center; }

  /* Expanded detail */
  .detail-frame { left: 215px; top: 886px; width: 340px; height: 290px; border-radius: 30px; background: #1d1f26; border: 2px solid #262a33; }
  .detail { left: 222px; top: 893px; width: 326px; height: 276px; border-radius: 24px; background: linear-gradient(180deg, #3a424d, var(--panel) 30%); }
  .detail-head { left: 239px; top: 913px; font-size: 6.8px; font-weight: 700; display: flex; width: 280px; }
  .detail-head .c1 { color: var(--teal); width: 34px; font-weight: 500; }
  .detail-head .c2 { width: 170px; }
  .detail-head .c3 { width: 41px; }
  .detail-head .c4 { color: var(--teal); font-weight: 500; }
  .detail-head .up { margin-left: 12px; color: var(--teal); font-size: 5px; }
  .why { left: 239px; top: 933px; font-size: 5.8px; }
  .ev-label { left: 243px; font-size: 6.5px; font-weight: 500; }
  .ev-source { left: 359px; font-size: 6.5px; font-weight: 700; }
  .teal { color: var(--teal); }
  .purple { color: #8a6cff; }

  .btn { display: flex; align-items: center; justify-content: center; gap: 5px; border-radius: 4px; font-size: 6.5px; color: var(--ink); background: #222833; }
  .btn svg { width: 7px; height: 8px; }
  .btn.teal-btn { border: 1.5px solid var(--teal); }
  .btn.purple-btn { border: 1.5px solid var(--purple); }
  .btn.large { font-size: 8.5px; }
  .btn.large svg { width: 9px; height: 10px; }

  .callout { background: #1b2027; display: flex; align-items: center; }
  .callout.cataract { left: 54px; top: 984px; width: 322px; height: 52px; border: 2px solid var(--teal); }
  .callout.hba1c { left: 395px; top: 1064px; width: 323px; height: 52px; border: 2px solid var(--purple); }
  .callout-key { position: absolute; font-size: 7.5px; font-weight: 500; }
  .callout-body { position: absolute; font-size: 6.2px; line-height: 8.5px; }
  .callout-body strong { display: block; font-size: 7.5px; font-weight: 500; margin-bottom: 1px; }

  .node { width: 40px; height: 40px; border-radius: 50%; border: 1px solid #3c3f62; background: #161729; display: flex; align-items: center; justify-content: center; }
</style>
</head>
<body>

<svg class="decor" width="768" height="1200" viewBox="0 0 768 1200" aria-hidden="true">
  <defs>
    <linearGradient id="dot" x1="0" y1="0" x2="0" y2="1">
      <stop offset="0" stop-color="#34c9dc"/><stop offset="1" stop-color="#1a6fb8"/>
    </linearGradient>
  </defs>
  <!-- top-left ring and dot -->
  <circle cx="190" cy="-55" r="98" fill="#151425" stroke="var(--line)" stroke-width="1"/>
  <circle cx="78" cy="-2" r="25" fill="url(#dot)"/>
  <path d="M280 6 C 320 20, 295 110, 360 125 L 406 139" fill="none" stroke="#3d3a66" stroke-width="1"/>
  <!-- compendium ring -->
  <circle cx="526" cy="178" r="121" fill="none" stroke="var(--line)" stroke-width="1"/>
  <!-- document outline -->
  <path d="M480 96 L 502 96 L 502 130 M 467 122 L 467 258 L 478 258 M 467 122 L 492 96" fill="none" stroke="#4a4f7a" stroke-width="1"/>
  <circle cx="406" cy="139" r="12" fill="url(#dot)"/>
  <circle cx="447" cy="270" r="12" fill="url(#dot)"/>
  <path d="M440 278 C 400 300, 380 310, 379 360 L 379 388" fill="none" stroke="#3d3a66" stroke-width="1"/>
  <!-- connectors -->
  <line x1="385" y1="842" x2="385" y2="886" stroke="#4a4d6a" stroke-width="1"/>
  <line x1="110" y1="1036" x2="110" y2="1200" stroke="var(--teal)" stroke-width="1.5"/>
  <line x1="659" y1="1116" x2="659" y2="1200" stroke="var(--purple)" stroke-width="1.5"/>
</svg>

<!-- Intro -->
<h2 class="abs intro-title">COMPENDIUM C-CDA</h2>
<p class="abs intro-text">The normalized data is unified into the Compendium C-CDA. Enhanced composite longitudinal record in C-CDA format, the industry standard for all interoperability initiatives.</p>
<div class="abs ccda-tag">C-CDA</div>

<div class="abs toc-shadow"></div>
<nav class="abs toc">
  <div class="toc-head"><span class="toc-icon"></span>Table of Contents<span class="caret"></span></div>
  <div class="toc-item active"><span class="toc-icon"></span>Insurance Provider</div>
  <div class="toc-item"><span class="toc-icon"></span>Problems</div>
  <div class="toc-item"><span class="toc-icon"></span>Results</div>
  <div class="toc-item"><span class="toc-icon"></span>Procedures</div>
  <div class="toc-item"><span class="toc-icon"></span>Encounters</div>
  <div class="toc-item"><span class="toc-icon"></span>Medications</div>
  <div class="toc-item"><span class="toc-icon"></span>Vital Signs</div>
  <div class="toc-item"><span class="toc-icon"></span>Immunizations</div>
  <div class="toc-item"><span class="toc-icon"></span>Social History</div>
  <div class="toc-item"><span class="toc-icon"></span>Family History</div>
  <div class="toc-item"><span class="toc-icon"></span>Plan of Care</div>
</nav>

<!-- Insights -->
<div class="abs insights"></div>
<h1 class="abs insights-title">SUMMARIZED AND LINKED<br>TO KEY INSIGHTS</h1>
<p class="abs insights-text">Insights are presented in a concise summary with direct links to supporting evidence. HCC opportunities are abstracted and cross-linked directly to the original text in the underlying record for quick and easy reference.</p>

<div class="abs dash-shadow"></div>
<section class="abs dash">
  <div class="dash-inner">
    <div class="abs brand"><span class="brand-mark"></span>NOVACHART</div>
    <div class="abs patient">Patient, MARY<br>| Female | 01/11/1951 &nbsp;| &nbsp;Age: 70</div>
    <div class="abs dash-title">C-CDA Compendium</div>
    <div class="abs hcc">HCC Summary</div>
    <div class="abs raf-line"><span class="teal">RAF: 1.462</span> | Condition Count: 5 | ID: 7326472</div>
    <table class="hcc-table">
      <tr><th class="code">ICC-10 Code</th><th>Condition</th><th class="cat">Category</th><th class="raf">RAF</th><th></th></tr>
      <tr><td class="code">J44.9</td><td class="cond">Chronic obstructive pulmonary disease</td><td class="cat">111</td><td class="raf">0.335</td><td class="arrow">▼</td></tr>
      <tr><td class="code">F33.1</td><td class="cond">Chronic kidney disease, moderate (stage 3)</td><td class="cat">138</td><td class="raf">0.069</td><td class="arrow">▼</td></tr>
      <tr><td class="code">F33.0</td><td class="cond">Major depressive disorder, recurrent, mild</td><td class="cat">59</td><td class="raf">0.309</td><td class="arrow">▼</td></tr>
      <tr><td class="code">I42.9</td><td class="cond">Cardiomyopathy</td><td class="cat">85</td><td class="raf">0.447</td><td class="arrow">▼</td></tr>
      <tr><td class="code">E11.36</td><td class="cond">Type 2 diabeters mellitus with diabetic cataract</td><td class="cat">18</td><td class="raf">0.302</td><td class="arrow">▼</td></tr>
    </table>
  </div>
</section>
<div class="abs hover-ring"></div>
<svg class="abs" style="left:503px;top:782px" width="12" height="12" viewBox="0 0 12 12" aria-hidden="true"><path d="M1 1 L11 5 L6 6 L5 11 Z" fill="var(--purple)"/></svg>
<div class="abs hover-badge">Hover Animation</div>

<!-- Expanded detail -->
<div class="abs detail-frame"></div>
<section class="abs detail"></section>
<div class="abs detail-head"><span class="c1">E11.36</span><span class="c2">Type 2 diabeters mellitus with diabetic cataract</span><span class="c3">18</span><span class="c4">0.302</span><span class="up">▲</span></div>
<p class="abs why"><strong>Why:</strong> This patient was treated for cataracts that may be associated witj type 2 diabetes mellitus</p>

<span class="abs ev-label teal" style="top:966px">Extracapsular Cataract with IOL</span>
<span class="abs ev-source" style="top:966px">C-CDA: PROCEDURES</span>
<a class="abs btn teal-btn" style="left:470px;top:960px;width:63px;height:21px">
  <svg viewBox="0 0 8 10"><path d="M1 .5h4l2 2v7H1z M2.5 4.5h3 M2.5 6h3 M2.5 7.5h3" fill="none" stroke="#fff" stroke-width=".8"/></svg>View source</a>

<span class="abs ev-label purple" style="top:1047px">Diabetes Type 2</span>
<span class="abs ev-source" style="top:1047px">C-CDA: PROBLEM LIST</span>
<a class="abs btn purple-btn" style="left:470px;top:1041px;width:63px;height:21px">
  <svg viewBox="0 0 8 10"><path d="M1 .5h4l2 2v7H1z M2.5 4.5h3 M2.5 6h3 M2.5 7.5h3" fill="none" stroke="#fff" stroke-width=".8"/></svg>View source</a>

<span class="abs ev-label purple" style="top:1128px">AntidiabeticDrug Class</span>
<span class="abs ev-source" style="top:1128px">C-CDA: PROBLEM LIST</span>
<a class="abs btn purple-btn" style="left:470px;top:1122px;width:63px;height:21px">
  <svg viewBox="0 0 8 10"><path d="M1 .5h4l2 2v7H1z M2.5 4.5h3 M2.5 6h3 M2.5 7.5h3" fill="none" stroke="#fff" stroke-width=".8"/></svg>View source</a>

<!-- Evidence callouts -->
<div class="abs callout cataract">
  <span class="callout-key teal" style="left:14px">Cataract</span>
  <div class="callout-body" style="left:94px"><strong class="teal">Ophthalmology chart note</strong>Patient presents for cataract<br>evalution in the right eye.</div>
  <a class="abs btn teal-btn large" style="left:230px;top:12px;width:78px;height:25px">
    <svg viewBox="0 0 8 10"><path d="M1 .5h4l2 2v7H1z M2.5 4.5h3 M2.5 6h3 M2.5 7.5h3" fill="none" stroke="#fff" stroke-width=".8"/></svg>View source</a>
</div>

<div class="abs callout hba1c">
  <span class="callout-key purple" style="left:14px">HbA1c</span>
  <div class="callout-body" style="left:130px"><strong class="purple">Lab results</strong>Hemoglobin A1C<br>6.9%<br>01/15/21</div>
  <a class="abs btn purple-btn large" style="left:230px;top:12px;width:77px;height:25px">
    <svg viewBox="0 0 8 10"><path d="M1 .5h4l2 2v7H1z M2.5 4.5h3 M2.5 6h3 M2.5 7.5h3" fill="none" stroke="#fff" stroke-width=".8"/></svg>View source</a>
</div>

<!-- Source nodes -->
<div class="abs node" style="left:90px;top:1109px">
  <svg width="20" height="18" viewBox="0 0 20 18" aria-label="Fax"><rect x="1" y="6" width="4" height="11" rx="1.5" fill="none" stroke="var(--teal)"/><rect x="5" y="6" width="14" height="11" rx="1.5" fill="none" stroke="var(--teal)"/><rect x="8" y="1" width="8" height="5" fill="none" stroke="var(--teal)"/><g fill="var(--teal)"><circle cx="10" cy="10" r=".7"/><circle cx="13" cy="10" r=".7"/><circle cx="16" cy="10" r=".7"/><circle cx="10" cy="13" r=".7"/><circle cx="13" cy="13" r=".7"/><circle cx="16" cy="13" r=".7"/></g></svg>
</div>
<div class="abs node" style="left:639px;top:1150px">
  <svg width="18" height="18" viewBox="0 0 18 18" aria-label="Test tube"><path d="M12 2 L16 6 M14 4 L5 13 A2.5 2.5 0 0 1 1.5 9.5 L10.5 .5" fill="none" stroke="#7c63ff" stroke-width="1.2"/><path d="M6 8 l1.5 1.5 M8 6 l1.5 1.5" stroke="#7c63ff"/></svg>
</div>

</body>
</html>
```